Black Matte card with samurai logo which I would like it to be textured and company name on one side and on the other side I would like the company information with the reno (Face logo) Sushi logo. Double Sided card.

majority customers are University students, University sororities and fraternities.

It Company

Reno Sushi
317 W. Harlow Ave
Tucson, AZ 85042
Phone (520)413-6271
Fax (520)357-1846
E-mail: Renosushidesert@mailbox-example.com
FB: Renosushidesert
Twitter: Renosushidesert

• Present Normal

```html
<!DOCTYPE html>
<html lang="en">
<head>
<meta charset="utf-8">
<title>Reno Sushi – Business Card</title>
<link rel="stylesheet" href="https://fonts.googleapis.com/css2?family=Kalam:wght@400&family=Open+Sans:wght@400;600&display=swap">
<style>
  :root {
    --page-bg: #ece8e3;
    --card-black: #1c1c1c;
    --card-grey: #3a3a3a;
    --card-white: #ffffff;
    --brand-red: #a8261f;
    --ink: #2b2b2b;
    --band: #262626;
    --rule: #c9c9c9;
    --social: #6d7f99;
    --logo-dark: #2a2a2a;
  }
  * { box-sizing: border-box; margin: 0; padding: 0; }
  html, body { width: 1200px; height: 950px; overflow: hidden; }
  body { background: var(--page-bg); position: relative; font-family: "Open Sans", Arial, sans-serif; }

  .card { position: absolute; width: 738px; height: 420px; overflow: hidden; box-shadow: 0 2px 6px rgba(0,0,0,.18); }

  /* Front: textured matte black */
  .card--front {
    left: 44px; top: 42px;
    background:
      repeating-linear-gradient(180deg, rgba(255,255,255,.05) 0 1px, rgba(0,0,0,0) 1px 5px, rgba(0,0,0,.25) 5px 7px, rgba(0,0,0,0) 7px 13px),
      repeating-linear-gradient(178.6deg, rgba(255,255,255,.04) 0 2px, rgba(0,0,0,0) 2px 19px, rgba(0,0,0,.35) 19px 21px, rgba(0,0,0,0) 21px 31px),
      radial-gradient(ellipse at 50% 35%, #4a4a4a 0%, #2a2a2a 55%, #0e0e0e 100%);
  }
  .card--front .logo-art {
    position: absolute; left: 235px; top: 30px; width: 265px; height: 240px;
    background: radial-gradient(closest-side, rgba(240,240,240,.95) 0%, rgba(170,170,170,.7) 55%, rgba(120,40,35,.35) 80%, rgba(40,40,40,0) 100%);
  }
  .card--front .brand-name {
    position: absolute; left: 0; right: 0; top: 288px; text-align: center;
    font-family: "Kalam", cursive; font-weight: 400; font-size: 64px; line-height: 1;
    color: var(--card-white);
  }

  /* Back */
  .card--back {
    left: 412px; top: 490px;
    background: var(--card-white); border: 1px solid var(--rule);
  }
  .card--back .logo-art {
    position: absolute; left: 108px; top: 56px; width: 196px; height: 164px;
    background: radial-gradient(closest-side, rgba(42,42,42,.95) 0%, rgba(90,60,58,.75) 55%, rgba(176,48,42,.3) 82%, rgba(255,255,255,0) 100%);
  }
  .card--back .brand-name {
    position: absolute; left: 96px; width: 220px; top: 218px; text-align: center;
    font-family: "Kalam", cursive; font-weight: 400; line-height: 1;
  }
  .brand-name__main { display: block; font-size: 56px; color: var(--brand-red); }
  .brand-name__sub { display: block; font-size: 30px; color: var(--ink); margin-top: -6px; }

  .divider { position: absolute; left: 369px; top: 117px; width: 1px; height: 148px; background: var(--rule); }

  .contact-list { position: absolute; left: 386px; top: 120px; list-style: none; }
  .contact-list li {
    display: flex; align-items: center; height: 27px;
    font-size: 17px; color: var(--ink); white-space: nowrap;
  }
  .contact-list .icon { width: 15px; height: 15px; margin-right: 9px; flex: none; }
  .contact-list .icon--social { background: var(--social); border-radius: 2px; width: 14px; height: 14px; }

  .footer-rule { position: absolute; left: 0; right: 0; height: 2px; }
  .footer-rule--red { top: 364px; background: var(--brand-red); }
  .footer-rule--grey { top: 369px; height: 1px; background: var(--rule); }
  .footer-band {
    position: absolute; left: 0; right: 0; bottom: 0; height: 46px; background: var(--band);
    color: var(--card-white); font-size: 18px; display: flex; align-items: center; justify-content: center;
  }
</style>
</head>
<body>

<section class="card card--front" aria-label="Card front">
  <div class="logo-art" role="img" aria-label="Samurai mascot holding a sword and a fish"></div>
  <p class="brand-name">reno sushi</p>
</section>

<section class="card card--back" aria-label="Card back">
  <div class="logo-art" role="img" aria-label="Samurai mascot holding a sword and a fish"></div>
  <p class="brand-name"><span class="brand-name__main">reno</span><span class="brand-name__sub">sushi</span></p>

  <div class="divider"></div>

  <ul class="contact-list">
    <li>
      <svg class="icon" viewBox="0 0 16 16" aria-hidden="true"><path fill="#a8261f" d="M4 1.5l2.2 3-1.3 1.6c.9 2 2.3 3.5 4.3 4.4l1.6-1.3 3 2.2-1.2 2.6C7.5 14 2 8.5 1.4 2.7z"/></svg>
      (520)413-6271
    </li>
    <li>
      <svg class="icon" viewBox="0 0 16 16" aria-hidden="true"><rect x="4" y="1" width="8" height="14" rx="1.5" fill="#a8261f"/><rect x="5.5" y="3" width="5" height="5" fill="#fff"/><circle cx="8" cy="12" r="1" fill="#fff"/></svg>
      (520)357-1846
    </li>
    <li>
      <svg class="icon" viewBox="0 0 16 16" aria-hidden="true"><rect x="1" y="3.5" width="14" height="10" rx="1" fill="#a8261f"/><path d="M1.5 4.2L8 9l6.5-4.8" fill="none" stroke="#fff" stroke-width="1.3"/></svg>
      Renosushidesert@mailbox-example.com
    </li>
    <li><span class="icon icon--social" aria-hidden="true"></span>Renosushidesert</li>
    <li><span class="icon icon--social" aria-hidden="true"></span>Renosushidesert</li>
  </ul>

  <div class="footer-rule footer-rule--red"></div>
  <div class="footer-rule footer-rule--grey"></div>
  <p class="footer-band">Reno Sushi 317 W. Harlow Ave Tucson, AZ 85042</p>
</section>

</body>
</html>
```